Corvane Business Cards

Front of business card will have logo, name, address, & telephone number. Back of card will have a list of services provided - Roads, Substation Pads, Temporary Pads, Site Pads, Land Leveling, Powerline Row Cleaning, Land Clearing, Gates, Fencing, Construction Entrances, Excavation, Trenching, Underground Utilities, Directional Boring, Pile Driving. We are a construction company that uses heavy equipment like bulldozers, motor graders/blades, dump trucks, backhoes, hydro axes, & skid loaders. We build roads, pads, & install electric utility lines & waterlines underground. This logo is new. The word "Construction" can be smaller as uploaded 2 example edited logos. We will be using this card design for many employees.
Target Market(s)
Industrial Electric Powerline, Wind Turbine, Solar Panel, & Water Utility companies.
Contact Information for Business Card
Name/Position - Dwayne Halster - Owner
Address: 4875 FM 309
Brannock, KS 67412
Phone number - (555) 482-5096

```html
<!DOCTYPE html>
<html lang="en">
<head>
<meta charset="utf-8">
<title>Corvane Business Cards</title>
<link rel="stylesheet" href="https://fonts.googleapis.com/css2?family=Arimo:wght@400;700&display=swap">
<style>
  :root {
    --maroon: #3a0f17;
    --ink: #2a2a2a;
    --card: #ffffff;
    --stage: #d4d4d4;
    --rule: #bdbdbd;
  }
  * { margin: 0; padding: 0; box-sizing: border-box; }
  html, body { width: 1200px; height: 802px; overflow: hidden; }
  body {
    background: var(--stage);
    font-family: "Arimo", Arial, sans-serif;
    position: relative;
  }
  .card {
    position: absolute;
    top: 274px;
    width: 443px;
    height: 264px;
    background: var(--card);
    overflow: hidden;
  }
  .card--front { left: 136px; }
  .card--back { left: 608px; background: var(--maroon); }

  /* Front */
  .brand {
    position: absolute;
    left: 32px;
    top: 94px;
    width: 196px;
    display: flex;
    align-items: center;
    gap: 8px;
    color: var(--maroon);
    font-weight: 700;
  }
  .brand__mark {
    width: 16px; height: 16px;
    background: var(--maroon);
    border-radius: 50%;
    flex: none;
  }
  .brand__name { font-size: 33px; line-height: 1; }
  .brand__name small { display: block; font-size: 15.5px; letter-spacing: 0.4px; margin-top: 5px; }
  .divider {
    position: absolute;
    left: 236px; top: 75px;
    width: 1.5px; height: 122px;
    background: var(--rule);
  }
  .contact { position: absolute; left: 250px; top: 77px; color: var(--ink); }
  .contact__name { font-size: 17px; font-weight: 700; color: var(--maroon); line-height: 1.1; }
  .contact__role { font-size: 12.5px; letter-spacing: 0.3px; margin-top: 1px; }
  .contact__phone { font-size: 18.5px; margin-top: 14px; }
  .contact__address { font-size: 14.5px; line-height: 1.35; margin-top: 12px; }

  /* Back */
  .services-panel {
    position: absolute;
    left: 0; top: 42px;
    width: 443px; height: 180px;
    background: var(--card);
    text-align: center;
    color: var(--maroon);
  }
  .services-panel h2 {
    font-weight: 400;
    font-size: 19.5px;
    margin-top: 30px;
  }
  .services-panel p {
    font-size: 13.2px;
    line-height: 19.5px;
    margin: 18px 34px 0;
  }
</style>
</head>
<body>
  <section class="card card--front">
    <div class="brand">
      <span class="brand__mark"></span>
      <span class="brand__name">CORVANE<small>CONSTRUCTION</small></span>
    </div>
    <div class="divider"></div>
    <div class="contact">
      <div class="contact__name">DWAYNE HALSTER</div>
      <div class="contact__role">OWNER</div>
      <div class="contact__phone">(555) 482-5096</div>
      <div class="contact__address">4875 FM 309<br>Brannock, KS 67412</div>
    </div>
  </section>

  <section class="card card--back">
    <div class="services-panel">
      <h2>Our Services</h2>
      <p>Roads | Substation Pads | Temporary Pads | Site Pads | Land Leveling, Powerline Row Cleaning | Land Clearing | Gates Fencing | Construction Entrances | Excavation | Trenching Underground Utilities | Directional Boring | Pile Driving.</p>
    </div>
  </section>
</body>
</html>
```